Create modern and sleek business card for luxury real estate company

We're a "boutique" real estate office looking for a design that gets across a highly modern luxury brand. Blacks and whites are probably the best colors unless we try a silver foil for the logo. I've attached a version of our current logo here. I'd like to swap out the current font on there with Gotham Light Regular.

I'm looking to have one side of the card have the logo with the space for our agents info on the other side.

Target Market(s)

Young professionals in a "luxury" headspace

Industry/Entity Type

Real estate

Contact Information for Business Card

A place for agent name, cell number, website. The slogan "Simply Reimagining Fine Homes".

Font styles to use
Other font styles liked:
• Gotham Regular

Colors

Designer to choose only greyscale colors for use in the design.

Requirements
Must have
• Matte black as the background color. Clean lines and use of contrast. A specific design aspect that will use silver foil.
Nice to have
• Up in the air on integrating a QR code
Should not have
• Any houses or other real estate related design (ex: a clip art house)

```html
<!DOCTYPE html>
<html lang="en">
<head>
<meta charset="utf-8">
<title>Meridian Realty – Business Card</title>
<link href="https://fonts.googleapis.com/css2?family=Montserrat:wght@300;400;500&display=swap" rel="stylesheet">
<style>
  :root{
    --page:#ffffff;
    --card:#000000;
    --silver:#e6e6e6;
    --text:#f2f2f2;
    --muted:#cfcfcf;
    --rule:#bdbdbd;
    --shadow:rgba(0,0,0,0.45);
  }
  *{margin:0;padding:0;box-sizing:border-box;}
  html,body{width:1200px;height:1200px;overflow:hidden;background:var(--page);}
  body{position:relative;font-family:"Montserrat",sans-serif;color:var(--text);}
  .card{position:absolute;left:250px;width:700px;height:400px;background:var(--card);
        box-shadow:14px 14px 16px var(--shadow);}
  .card--front{top:147px;}
  .card--back{top:653px;}
  .brand{position:absolute;display:flex;align-items:center;transform:translateY(-50%);}
  .brand__circle{border:2px solid var(--silver);border-radius:50%;flex:none;}
  .brand__name{font-weight:400;color:var(--silver);text-transform:uppercase;line-height:1.05;letter-spacing:1px;}
  .card--front .brand{left:175px;top:196px;}
  .card--front .brand__circle{width:100px;height:100px;margin-right:20px;}
  .card--front .brand__name{font-size:42px;}
  .card--back .brand{left:39px;top:182px;}
  .card--back .brand__circle{width:76px;height:76px;margin-right:16px;}
  .card--back .brand__name{font-size:32px;}
  .front__web{position:absolute;left:0;right:0;top:360px;text-align:center;font-size:14px;
              font-weight:400;letter-spacing:4px;color:var(--muted);}
  .back__divider{position:absolute;left:355px;top:110px;width:1px;height:167px;background:var(--rule);}
  .agent{position:absolute;left:387px;top:80px;}
  .agent__name{font-size:27px;font-weight:500;letter-spacing:0.5px;color:var(--text);}
  .agent__title{font-size:13px;font-weight:400;letter-spacing:1px;color:var(--muted);margin-top:2px;}
  .contact{position:absolute;left:404px;top:155px;list-style:none;}
  .contact__item{display:flex;align-items:center;height:35.5px;font-size:13px;letter-spacing:0.8px;color:var(--text);white-space:nowrap;}
  .contact__icon{width:18px;height:18px;margin-right:18px;flex:none;}
  .back__slogan{position:absolute;left:0;right:0;top:352px;text-align:center;font-size:18px;
                font-weight:400;letter-spacing:3px;color:var(--text);}
</style>
</head>
<body>
  <section class="card card--front">
    <div class="brand">
      <span class="brand__circle"></span>
      <span class="brand__name">Meridian<br>Realty</span>
    </div>
    <p class="front__web">www.northgateboston.com</p>
  </section>

  <section class="card card--back">
    <div class="brand">
      <span class="brand__circle"></span>
      <span class="brand__name">Meridian<br>Realty</span>
    </div>
    <div class="back__divider"></div>
    <div class="agent">
      <h1 class="agent__name">Daniel Reyes</h1>
      <p class="agent__title">Company Agent</p>
    </div>
    <ul class="contact">
      <li class="contact__item">
        <svg class="contact__icon" viewBox="0 0 24 24" fill="none" stroke="#f2f2f2" stroke-width="1.4" stroke-linejoin="round"><path d="M5 3h4l2 5-2.5 1.5a11 11 0 0 0 6 6L16 13l5 2v4a2 2 0 0 1-2 2A16 16 0 0 1 3 5a2 2 0 0 1 2-2z"/></svg>
        617-555-0142
      </li>
      <li class="contact__item">
        <svg class="contact__icon" viewBox="0 0 24 24" fill="none" stroke="#f2f2f2" stroke-width="1.4"><rect x="2" y="5" width="20" height="14"/><path d="M2 5l10 8 10-8M2 19l7-7M22 19l-7-7"/></svg>
        hello@northgateboston.com
      </li>
      <li class="contact__item">
        <svg class="contact__icon" viewBox="0 0 24 24" fill="none" stroke="#f2f2f2" stroke-width="1.4"><path d="M12 22s7-7 7-12a7 7 0 0 0-14 0c0 5 7 12 7 12z"/><circle cx="12" cy="10" r="2.6"/></svg>
        Meridian Realty, 48 Harbor Lane
      </li>
      <li class="contact__item">
        <svg class="contact__icon" viewBox="0 0 24 24" fill="none" stroke="#f2f2f2" stroke-width="1.4" stroke-linejoin="round"><path d="M6 3l0 16 4-4 3 6 2.5-1-3-6h5.5z"/></svg>
        www.northgateboston.com
      </li>
    </ul>
    <p class="back__slogan">Simply Reimagining Fine Homes</p>
  </section>
</body>
</html>
```